One Page Website for Personal Trainer in London

I have a logo and need a one page website designed around my branding. I am a freelance Personal Trainer based in London specialising in bodyweight training for men and women. I would like the site to be modern and clean but not overtly urban in design.
I need the following headings:
About Me
My Services
Events
Blog
I don't need them to be seperate pages but if they can link to further down the page that would be great.
Industry/Entity Type
Personal Trainer
Coding
Coded - Design and coding required
Number of Pages Required
1 page
Requirements
Must have
- I need the following headings:
- About Me
- My Services
- Events
- Blog
- mobile friendly formatting
- health and fitness related photography
- Colour scheme in keeping with my existing logo

```html
<!DOCTYPE html>
<html lang="en">
<head>
<meta charset="utf-8">
<title>Marlowe Grant – Personal Training</title>
<meta name="viewport" content="width=1200">
<link href="https://fonts.googleapis.com/css2?family=Open+Sans:ital,wght@0,400;0,600;0,700;1,600&display=swap" rel="stylesheet">
<style>
:root{
  --orange:#f7931e;
  --orange-dark:#e5830f;
  --ink:#222222;
  --text:#555555;
  --muted:#8a8a8a;
  --light:#f2f2f2;
  --white:#ffffff;
  --footer:#2a2a2a;
  --rule:#dddddd;
}
*{box-sizing:border-box;margin:0;padding:0}
html,body{width:1200px;height:3863px;overflow:hidden}
body{font-family:"Open Sans",Arial,sans-serif;color:var(--text);background:var(--white);position:relative}
section,header,footer{position:absolute;left:0;width:1200px}
.abs{position:absolute}
.btn{position:absolute;display:flex;align-items:center;justify-content:center;background:var(--orange);color:var(--white);font-weight:600;text-transform:uppercase;text-decoration:none}
.accent-line{position:absolute;height:4px;width:40px;background:var(--orange)}

/* Hero */
.hero{top:0;height:798px;background:linear-gradient(120deg,#3c3a38 0%,#5a5550 40%,#4a4642 70%,#2f2d2c 100%)}
.hero-photo{position:absolute;inset:0;background:radial-gradient(ellipse at 75% 40%,rgba(120,110,100,.55),transparent 60%),radial-gradient(ellipse at 25% 50%,rgba(100,95,90,.5),transparent 55%)}
.nav-bar{position:absolute;top:39px;left:0;width:1200px;height:59px;background:rgba(20,20,20,.55)}
.brand{position:absolute;top:0;left:52px;width:283px;height:185px;background:rgba(255,255,255,.9);display:flex;flex-direction:column;align-items:center;justify-content:center;gap:8px}
.brand-mark{width:34px;height:34px;border-radius:50%;background:var(--orange)}
.brand-name{font-size:30px;font-weight:700;color:var(--orange);line-height:1}
.brand-tag{font-size:12px;letter-spacing:3px;color:var(--ink);text-transform:uppercase;border-top:1px solid var(--ink);padding-top:4px}
.nav{position:absolute;top:56px;right:92px;display:flex;font-size:15px;color:var(--white)}
.nav a{color:var(--white);text-decoration:none;padding:0 12px;border-left:1px solid rgba(255,255,255,.7);line-height:18px}
.nav a:first-child{border-left:0}
.nav a.active{color:var(--orange)}
.hero-copy{position:absolute;top:340px;left:0;width:1200px;text-align:center;color:var(--white);padding-left:200px}
.hero-copy .lead{font-size:46px;line-height:56px}
.hero-copy .big{font-size:70px;font-weight:700;color:var(--orange);line-height:80px}
.hero-copy .sub{font-size:36px;line-height:44px}
.hero .btn{top:541px;left:530px;width:227px;height:56px;font-size:22px;text-transform:none;font-weight:400}

/* About */
.about{top:798px;height:533px}
.section-title{font-size:42px;font-weight:700;color:var(--ink)}
.about .section-title{position:absolute;top:78px;left:126px}
.about .accent-line{top:148px;left:120px;width:30px}
.about-heading{position:absolute;top:172px;left:120px;width:420px;font-size:15px;font-weight:600;color:var(--ink);text-transform:uppercase;line-height:20px}
.about-text{position:absolute;top:243px;left:120px;width:420px;font-size:12.5px;line-height:19px;color:var(--muted)}
.about .btn{top:376px;left:118px;width:168px;height:36px;font-size:12px}
.about-photo{position:absolute;top:90px;left:646px;width:412px;height:312px;background:linear-gradient(180deg,#f3d9a4 0%,#d8b479 35%,#8a9a55 70%,#6b7a3d 100%)}

/* Band */
.band{top:1331px;height:479px;background:linear-gradient(90deg,#3a3a3a,#5b5957 50%,#3d3c3b)}
.band-photo{position:absolute;inset:0;background:radial-gradient(ellipse at 50% 55%,rgba(150,140,130,.35),transparent 60%)}
.band-copy{position:absolute;top:150px;left:0;width:1200px;text-align:center;color:var(--white)}
.band-copy .intro{font-size:22px;font-style:italic;font-weight:600}
.band-copy .headline{font-size:56px;font-weight:600;line-height:62px;margin-top:12px}

/* Services */
.services{top:1810px;height:590px}
.centered-title{position:absolute;left:0;width:1200px;text-align:center}
.services .section-title{top:60px}
.services .accent-line{top:127px;left:585px;width:30px}
.service-card{position:absolute;top:178px;width:268px;text-align:center}
.service-photo{width:268px;height:175px}
.service-name{margin-top:18px;font-size:17px;font-weight:700;color:var(--orange)}
.service-text{margin-top:4px;font-size:11.5px;line-height:15px;color:var(--text);padding:0 4px}
.services .btn{top:474px;left:523px;width:165px;height:36px;font-size:12px}

/* Blog */
.blog{top:2400px;height:713px;background:var(--orange)}
.blog .section-title{color:var(--white);top:57px}
.blog .accent-line{background:var(--white);top:136px;left:588px;width:24px;height:3px}
.post{position:absolute;top:188px;width:265px;height:327px;background:var(--white);border-radius:6px;overflow:hidden}
.post-photo{width:265px;height:188px}
.post-date{position:absolute;top:0;left:0;width:48px;height:58px;background:var(--orange);color:var(--white);text-align:center;border:2px solid var(--white);border-top:0;border-left:0}
.post-date b{display:block;font-size:26px;line-height:34px}
.post-date span{font-size:8px;display:block}
.post-title{padding:14px 16px 0;font-size:16px;font-weight:600;color:var(--ink);line-height:20px}
.post-text{padding:8px 16px 0;font-size:10.5px;line-height:14px;color:var(--muted)}
.blog .btn-light{position:absolute;top:592px;left:518px;width:167px;height:39px;background:var(--white);color:var(--ink);font-size:11px;font-weight:600;display:flex;align-items:center;justify-content:center;text-transform:uppercase}

/* Events & testimonials */
.lower{top:3113px;height:430px;background:var(--light)}
.col-title{position:absolute;font-size:28px;font-weight:700;color:var(--orange)}
.arrows{position:absolute;display:flex;gap:6px}
.arrows svg{display:block}
.col-rule{position:absolute;height:2px;background:var(--rule)}
.event{position:absolute;left:98px;width:457px}
.event-date{position:absolute;left:0;top:0;width:62px;height:77px;text-align:center}
.event-date b{display:block;height:48px;background:#333333;color:var(--white);font-size:24px;line-height:48px}
.event-date span{display:block;height:29px;background:var(--orange);color:var(--white);font-size:15px;line-height:29px}
.event-title{position:absolute;left:95px;top:2px;font-size:15px;font-weight:600;color:var(--ink)}
.event-text{position:absolute;left:95px;top:28px;width:360px;font-size:12px;line-height:16px;color:var(--text)}
.divider-v{position:absolute;left:604px;top:80px;width:1px;height:300px;background:var(--rule)}
.client-photo{position:absolute;left:662px;top:142px;width:139px;height:139px;border-radius:50%;background:linear-gradient(180deg,#e9e4e0,#c9b7aa);border:4px solid var(--white)}
.client-name{position:absolute;left:662px;top:290px;width:139px;text-align:center;font-size:13px;font-weight:700;color:var(--orange);text-transform:uppercase}
.quote{position:absolute;left:826px;top:138px;width:306px;font-size:12px;line-height:17px;color:var(--text)}
.quote .mark{color:var(--orange);font-size:26px;font-weight:700;line-height:0;vertical-align:-8px}

/* Footer */
.site-footer{top:3543px;height:320px;background:var(--footer);text-align:center}
.address{position:absolute;top:70px;left:0;width:1200px;font-size:17px;font-weight:700;color:var(--white)}
.phone{position:absolute;top:97px;left:0;width:1200px;font-size:17px;font-weight:700;color:var(--orange)}
.social{position:absolute;top:168px;left:540px;display:flex;gap:22px}
.social span{width:14px;height:14px;border-radius:50%;background:var(--white);display:block}
.copyright{position:absolute;top:230px;left:0;width:1200px;font-size:10px;color:#8a8a8a}
</style>
</head>
<body>

<header class="hero" id="home">
  <div class="hero-photo" role="img" aria-label="Photo of two women doing bodyweight exercises in a gym"></div>
  <div class="nav-bar"></div>
  <div class="brand">
    <span class="brand-mark"></span>
    <span class="brand-name">Marlowe Grant</span>
    <span class="brand-tag">Personal Training</span>
  </div>
  <nav class="nav">
    <a href="#home" class="active">Home</a>
    <a href="#about">About Me</a>
    <a href="#services">My Services</a>
    <a href="#events">Events</a>
    <a href="#blog">Blog</a>
  </nav>
  <div class="hero-copy">
    <div class="lead">Start adding</div>
    <div class="big">Body weight Movements</div>
    <div class="sub">into your training &amp; enjoy the results!</div>
  </div>
  <a href="#services" class="btn">Start training Now</a>
</header>

<section class="about" id="about">
  <h2 class="section-title">About us</h2>
  <span class="accent-line"></span>
  <p class="about-heading">Negare non possum. Dolere malum est: in crucem qui agitur, beatus esse non potest. Quae cum dixisset paulumque institisset</p>
  <p class="about-text">Training with your own body weight builds strength, balance and control without a single machine. Every session is shaped around your goals, your pace and your week, so progress feels steady and sessions stay fun, safe and simple to keep up.</p>
  <a href="#services" class="btn">Read more</a>
  <div class="about-photo" role="img" aria-label="Photo of a woman stretching on grass at sunrise with palm trees"></div>
</section>

<section class="band">
  <div class="band-photo" role="img" aria-label="Photo of a man and woman doing squats in a bright gym"></div>
  <div class="band-copy">
    <p class="intro">I am a freelance Personal Trainer based in London specialising in</p>
    <p class="headline">Bodyweight training for<br>men and women.</p>
  </div>
</section>

<section class="services" id="services">
  <h2 class="section-title centered-title">Our Service</h2>
  <span class="accent-line"></span>
  <div class="service-card" style="left:170px">
    <div class="service-photo" role="img" aria-label="Photo of a woman lunging on a beach" style="background:linear-gradient(180deg,#b9c9d8,#7f93a6 60%,#9aa4ab)"></div>
    <div class="service-name">Stretching</div>
    <p class="service-text">Gentle mobility work to open hips, ease tension and move freely.</p>
  </div>
  <div class="service-card" style="left:466px">
    <div class="service-photo" role="img" aria-label="Photo of a man training with dumbbells" style="background:linear-gradient(180deg,#6d8fa8,#3f5a70 60%,#52606a)"></div>
    <div class="service-name">Bodyweight Exercise</div>
    <p class="service-text">Push, pull and squat patterns built up step by step for real strength.</p>
  </div>
  <div class="service-card" style="left:765px">
    <div class="service-photo" role="img" aria-label="Photo of trainers, weights and fitness gear on a grey floor" style="background:linear-gradient(180deg,#8f9499,#6c7177 60%,#7a7f84)"></div>
    <div class="service-name">Fitness Plans</div>
    <p class="service-text">Clear weekly plans that fit your schedule and keep you on track.</p>
  </div>
  <a href="#services" class="btn">More service</a>
</section>

<section class="blog" id="blog">
  <h2 class="section-title centered-title">Latest Blog</h2>
  <span class="accent-line"></span>

  <article class="post" style="left:44px">
    <div class="post-photo" role="img" aria-label="Photo of a woman resting after a workout" style="background:linear-gradient(135deg,#6fa3c4,#3e6f8f 60%,#c45a7a)"></div>
    <div class="post-date"><b>22</b><span>October</span></div>
    <h3 class="post-title">Negare non possum. Dolere malum est</h3>
    <p class="post-text">Three simple warm up moves that prepare joints and muscles for work.</p>
  </article>
  <article class="post" style="left:327px">
    <div class="post-photo" role="img" aria-label="Photo of two people running outdoors" style="background:linear-gradient(135deg,#c9c2b4,#9c927f 60%,#6d6455)"></div>
    <div class="post-date"><b>23</b><span>October</span></div>
    <h3 class="post-title">Quod autem satis est, eo quic uid accessit</h3>
    <p class="post-text">Why short daily sessions often beat one long workout each week.</p>
  </article>
  <article class="post" style="left:610px">
    <div class="post-photo" role="img" aria-label="Photo of a woman lifting a small dumbbell" style="background:linear-gradient(135deg,#b7c8a6,#8fa989 50%,#7a6fa0)"></div>
    <div class="post-date"><b>24</b><span>October</span></div>
    <h3 class="post-title">Alios in primisque familiarem nostrum Posidonium</h3>
    <p class="post-text">How to build a strong core without sit ups or any equipment.</p>
  </article>
  <article class="post" style="left:894px">
    <div class="post-photo" role="img" aria-label="Photo of a woman resting after a workout" style="background:linear-gradient(135deg,#6fa3c4,#3e6f8f 60%,#c45a7a)"></div>
    <div class="post-date"><b>24</b><span>October</span></div>
    <h3 class="post-title">Vicimus. Hanc ergo intuens debet institutum</h3>
    <p class="post-text">Eating well around training, with easy ideas for busy weekdays.</p>
  </article>

  <a href="#blog" class="btn-light">View all blog posts</a>
</section>

<section class="lower" id="events">
  <h2 class="col-title" style="left:93px;top:60px">Events</h2>
  <div class="arrows" style="left:515px;top:74px">
    <svg width="16" height="16" viewBox="0 0 16 16"><circle cx="8" cy="8" r="8" fill="#f7931e"/><path d="M9.5 4.5 6 8l3.5 3.5" fill="none" stroke="#fff" stroke-width="2"/></svg>
    <svg width="16" height="16" viewBox="0 0 16 16"><circle cx="8" cy="8" r="8" fill="#f7931e"/><path d="M6.5 4.5 10 8l-3.5 3.5" fill="none" stroke="#fff" stroke-width="2"/></svg>
  </div>
  <span class="col-rule" style="left:93px;top:119px;width:462px"></span>

  <div class="event" style="top:152px">
    <div class="event-date"><b>30</b><span>Oct</span></div>
    <div class="event-title">Verum tamen cum de rebus</div>
    <p class="event-text">Outdoor group session in the park, open to every level of fitness.</p>
  </div>
  <span class="col-rule" style="left:193px;top:242px;width:362px;height:1px"></span>
  <div class="event" style="top:250px">
    <div class="event-date"><b>31</b><span>Oct</span></div>
    <div class="event-title">Verum tamen cum de rebus</div>
    <p class="event-text">Evening mobility workshop focused on hips, back and shoulders.</p>
  </div>

  <span class="divider-v"></span>

  <h2 class="col-title" style="left:662px;top:60px">Testimonials</h2>
  <div class="arrows" style="left:1076px;top:74px">
    <svg width="16" height="16" viewBox="0 0 16 16"><circle cx="8" cy="8" r="8" fill="#f7931e"/><path d="M9.5 4.5 6 8l3.5 3.5" fill="none" stroke="#fff" stroke-width="2"/></svg>
    <svg width="16" height="16" viewBox="0 0 16 16"><circle cx="8" cy="8" r="8" fill="#f7931e"/><path d="M6.5 4.5 10 8l-3.5 3.5" fill="none" stroke="#fff" stroke-width="2"/></svg>
  </div>
  <span class="col-rule" style="left:662px;top:119px;width:458px"></span>

  <div class="client-photo" role="img" aria-label="Portrait photo of a smiling client"></div>
  <div class="client-name">Clara</div>
  <p class="quote"><span class="mark">“</span> After years of gym plans I never kept, these sessions finally stuck. I feel stronger, move better and actually look forward to training each week. Every workout is clear, friendly and pitched just right for me, and the progress has been steady from the very first month. I would recommend it to anyone. <span class="mark">”</span></p>
</section>

<footer class="site-footer">
  <p class="address">4120 Elmstead Road, London SE1 7QT</p>
  <p class="phone">Phone (555) 014 2290</p>
  <div class="social" aria-label="Social links"><span></span><span></span><span></span><span></span></div>
  <p class="copyright">© 2017 All rights reserved by Marlowe Grant</p>
</footer>

</body>
</html>
```